Business Card design for law firm = Brightvale Australia

We are seeking a new design for our business cards.
We are keeping our logo, which is attached.
We need space for
Name
Title
Address is , which is
Level 7
214 Marlowe Street
Sydney NSW 2047
Phone :
Mobile :
Fax :
Email :
DX :
website www.brightvale-example.com.au

Industry/Entity Type

Law Firm / Banking and Finance

Contact Information for Business Card

We are seeking a new design for our business cards. We are keeping our logo. We need space for Name Title Address is Level 7 214 Marlowe Street Sydney NSW 2047 Phone Mobile Fax Email DX website www.brightvale-example.com.au

Colors
0054AA
0677BA
7BADD7
CADEEF
E8F1F8

Requirements
Must have
• see our website for general feel www.brightvale-example.com.au

```html
<!DOCTYPE html>
<html lang="en">
<head>
<meta charset="utf-8">
<title>Brightvale Australia – Business Card</title>
<link rel="stylesheet" href="https://fonts.googleapis.com/css2?family=EB+Garamond:ital,wght@0,400;1,400&display=swap">
<style>
  :root {
    --backdrop: #2b2b2c;
    --card: #1e1f21;
    --card-edge: #26272a;
    --royal: #2f4e9e;
    --cyan: #0a93c9;
    --ink-light: #f1f1f1;
    --emboss: #3a3b3f;
  }
  * { margin: 0; padding: 0; box-sizing: border-box; }
  html, body { width: 1200px; height: 1138px; overflow: hidden; background: var(--backdrop); }
  .canvas { position: relative; width: 1200px; height: 1138px; }

  .card {
    position: absolute;
    width: 620px;
    height: 376px;
    border-radius: 16px;
    background: linear-gradient(160deg, var(--card-edge), var(--card) 60%);
    overflow: hidden;
    box-shadow: 0 4px 10px rgba(0,0,0,0.45);
  }
  .card--back { left: 272px; top: 184px; }
  .card--front { left: 274px; top: 606px; }

  .back-name {
    position: absolute;
    left: 0; right: 0; top: 150px;
    text-align: center;
    font-family: "EB Garamond", serif;
    font-size: 62px;
    color: var(--emboss);
  }

  .brand-name {
    position: absolute; left: 42px; top: 120px;
    font-family: "EB Garamond", serif;
    font-size: 48px; line-height: 1;
    color: var(--royal);
  }

  .person { position: absolute; right: 36px; top: 48px; text-align: right; font-family: "EB Garamond", serif; }
  .person-name { font-size: 28px; line-height: 1.1; color: var(--royal); }
  .person-title { font-size: 16px; font-style: italic; color: var(--cyan); }
  .address { margin-top: 14px; font-size: 15.5px; line-height: 1.3; color: var(--ink-light); }

  .contact-band {
    position: absolute; left: 0; right: 0; bottom: 0;
    height: 118px;
    background: var(--royal);
    border-top: 4px solid var(--cyan);
  }

  .contacts {
    position: absolute; right: 36px; top: 274px;
    list-style: none;
    font-family: "EB Garamond", serif;
    font-size: 15.5px; line-height: 20px;
    color: var(--ink-light);
    text-align: right;
  }
  .contacts li { display: flex; justify-content: flex-end; align-items: center; gap: 9px; }
  .contacts svg { width: 12px; height: 12px; fill: var(--ink-light); flex: none; }
</style>
</head>
<body>
<main class="canvas">

  <section class="card card--back" aria-label="Card back">
    <p class="back-name">Brightvale</p>
  </section>

  <section class="card card--front" aria-label="Card front">
    <div class="contact-band"></div>

    <p class="brand-name">Brightvale</p>

    <div class="person">
      <p class="person-name">Sam Calloway</p>
      <p class="person-title">Managing Director</p>
      <p class="address">Level 7 214 Marlowe St<br>Sydney NSW 2047</p>
    </div>

    <ul class="contacts">
      <li>02 9400 1185
        <svg viewBox="0 0 12 12"><path d="M1 4 Q6 0 11 4 L10 5.5 L8 5 L8 4 Q6 3 4 4 L4 5 L2 5.5 Z M3 6 H9 L10 11 H2 Z"/></svg>
      </li>
      <li>02 9400 1186
        <svg viewBox="0 0 12 12"><path d="M3 1 H9 V4 H3 Z M1 4.5 H11 V9 H9 V7 H3 V9 H1 Z M3.5 7.5 H8.5 V11 H3.5 Z"/></svg>
      </li>
      <li>www.brightvale-example.com.au
        <svg viewBox="0 0 12 12"><path d="M1 2.5 H11 V9.5 H1 Z" fill="none" stroke="#f1f1f1" stroke-width="1.2"/><path d="M1 2.5 L6 6.5 L11 2.5" fill="none" stroke="#f1f1f1" stroke-width="1.2"/></svg>
      </li>
      <li>sam.calloway@brightvale-example.com.au
        <svg viewBox="0 0 12 12"><circle cx="6" cy="6" r="5" fill="none" stroke="#f1f1f1" stroke-width="1.2"/><path d="M1 6 H11 M6 1 V11 M6 1 Q2.5 6 6 11 M6 1 Q9.5 6 6 11" fill="none" stroke="#f1f1f1" stroke-width="0.9"/></svg>
      </li>
    </ul>
  </section>

</main>
</body>
</html>
```